Harborview Estates Business Card for Apartment Buildings

Create business cards for resident managers who run apartment buildings. The audience is the public who are searching for apartment rentals, and current residents who live at the apartment building. Key design element will be incorporating the company logo, however, the logo cannot dominate. The building name and manager name are more important than the logo. Current business card design leaves little room for copy, so we may need to reduce the size on the current card to allow for more space for copy.

Target Market(s)

Adults 18-65 years of age, who are looking for an apartment rental, plus current residents who live at our apartment buildings.

Industry/Entity Type

Property Management

Contact Information for Business Card

A major design element will be use of the company logo. Important property and manager contact information must be part of the design. The size of the logo will need to be reduced to make room for building and manager contact copy.

Font styles to use
Sans Serif

Colors
3176b5
000000
959595
ffffff

Requirements
Must have
• 1) Incorporate the company logo.
• 2) Use the company colors (dark blue, black/grey, over white).
• 3) FEATURE THE BUILDING NAME
• 4) FEATURE THE MANAGER NAME
• 5) The company name is less important than BUILDING and MANAGER
• 6) Manager contact information
• **SEE ATTACHED CREATIVE BRIEF**
Nice to have
• 1) Back of card logo watermark
• 2) Ability to write notes on back of carfd
Should not have
• Avoid letting the company logo dominate the card, the building name and manager are more important than the company logo.

```html
<!DOCTYPE html>
<html lang="en">
<head>
<meta charset="utf-8">
<title>Harborview Estates – Resident Manager Business Card</title>
<link rel="stylesheet" href="https://fonts.googleapis.com/css2?family=Roboto:wght@400;500;700&display=swap">
<style>
  :root {
    --brand-blue: #1f6aa5;
    --ink: #3a3a3a;
    --ink-soft: #4a4a4a;
    --card: #f2f2f2;
    --backdrop: #262626;
    --shadow: rgba(0, 0, 0, 0.55);
  }
  html, body {
    margin: 0;
    width: 1200px;
    height: 960px;
    overflow: hidden;
    background: var(--backdrop);
    font-family: "Roboto", Arial, sans-serif;
  }
  .canvas { position: relative; width: 1200px; height: 960px; }
  .card {
    position: absolute;
    width: 600px;
    height: 343px;
    background: var(--card);
    box-shadow: 0 2px 6px var(--shadow);
    overflow: hidden;
  }
  .card--front { left: 314px; top: 113px; }
  .card--back { left: 311px; top: 472px; }

  .accent-band {
    position: absolute;
    left: 0; top: 34px;
    width: 46px; height: 77px;
    background: var(--brand-blue);
  }
  .brand {
    position: absolute;
    display: flex;
    align-items: center;
    gap: 12px;
  }
  .brand__square { width: 36px; height: 36px; background: var(--brand-blue); flex: none; }
  .brand__name {
    color: var(--brand-blue);
    font-weight: 700;
    font-size: 25px;
    letter-spacing: 0.5px;
    white-space: nowrap;
  }
  .card--front .brand { left: 58px; top: 55px; }

  .manager { position: absolute; left: 43px; top: 148px; }
  .manager__name { margin: 0; color: var(--brand-blue); font-size: 22px; font-weight: 500; letter-spacing: -0.2px; }
  .manager__title { margin: 2px 0 0; color: var(--ink); font-size: 14px; font-weight: 500; }

  .contact-list {
    position: absolute; left: 43px; top: 217px;
    margin: 0; padding: 0; list-style: none;
    color: var(--ink-soft); font-size: 14px;
  }
  .contact-list li { display: flex; align-items: center; height: 19px; }
  .contact-list svg { width: 13px; height: 13px; margin-right: 10px; fill: var(--brand-blue); flex: none; }

  .property {
    position: absolute; right: 39px; top: 250px;
    text-align: right;
  }
  .property__name { margin: 0; color: var(--brand-blue); font-size: 21px; font-weight: 500; }
  .property__address { margin: 2px 0 0; color: var(--ink-soft); font-size: 14px; line-height: 19px; font-style: normal; }

  .card--back .brand { right: 36px; top: 236px; }
  .card--back .brand__name { font-size: 24px; }
  .tagline {
    position: absolute; right: 36px; top: 290px;
    margin: 0; color: var(--ink); font-size: 14px; font-weight: 700;
  }
</style>
</head>
<body>
<main class="canvas">
  <section class="card card--front" aria-label="Business card front">
    <div class="accent-band"></div>
    <div class="brand">
      <span class="brand__square"></span>
      <span class="brand__name">HARBORVIEW ESTATES</span>
    </div>

    <div class="manager">
      <h1 class="manager__name">Marisol Delgado</h1>
      <p class="manager__title">Resident Manager</p>
    </div>

    <ul class="contact-list">
      <li><svg viewBox="0 0 16 16" aria-hidden="true"><path d="M3.6 1.2l2.3 2.6-1.3 1.9c.9 2.1 2.6 3.8 4.7 4.7l1.9-1.3 2.6 2.3-1.4 2.3C6.6 14.5 1.5 9.4 1.3 2.6z"/></svg>555-210-4431</li>
      <li><svg viewBox="0 0 16 16" aria-hidden="true"><path d="M4.5 0h7a1 1 0 0 1 1 1v14a1 1 0 0 1-1 1h-7a1 1 0 0 1-1-1V1a1 1 0 0 1 1-1zm1 2v10h5V2zm2.5 11a1 1 0 1 0 0 2 1 1 0 0 0 0-2z"/></svg>555-318-7702</li>
      <li><svg viewBox="0 0 16 16" aria-hidden="true"><path d="M4 1h8v4H4zM1 6h14v6h-2v-2H3v2H1zm3 5h8v4H4z"/></svg>555-406-9915</li>
      <li><svg viewBox="0 0 16 16" aria-hidden="true"><path d="M1 3h14v10H1zm1.5 1.5v.4L8 8.7l5.5-3.8v-.4z"/></svg>marisol@harborviewest.com</li>
      <li><svg viewBox="0 0 16 16" aria-hidden="true"><circle cx="8" cy="8" r="7"/></svg>www.harborviewest.com</li>
    </ul>

    <div class="property">
      <h2 class="property__name">Cedar Court Apartments</h2>
      <address class="property__address">1482 Linden Avenue<br>Fairhaven, CA 90210</address>
    </div>
  </section>

  <section class="card card--back" aria-label="Business card back">
    <div class="brand">
      <span class="brand__square"></span>
      <span class="brand__name">HARBORVIEW ESTATES</span>
    </div>
    <p class="tagline">Multifamily Property Management</p>
  </section>
</main>
</body>
</html>
```